Business Card Design for Software Development Company

I am looking for a business card design the incorporates my new logo (attached below).

Key information to include:
Name: Martin Quelbrook
Title: CEO
Email: martin@brightwellcivic.example
Phone: 555-218-9403
Website: www.brightwellcivic.example

NOTE: This design should be easy to edit so that we can order cards for different members of our team.

```html
<!DOCTYPE html>
<html lang="en">
<head>
<meta charset="utf-8">
<title>Brightwell Business Card</title>
<link rel="stylesheet" href="https://fonts.googleapis.com/css2?family=Source+Sans+3:wght@400;600;700&display=swap">
<style>
  :root {
    --bg: #1f1f1f;
    --paper: #fbfbfa;
    --ink: #1d1d1d;
    --teal: #13b29c;
    --orange: #e8782a;
    --rule: #f2c08e;
  }
  * { box-sizing: border-box; margin: 0; padding: 0; }
  html, body { width: 1200px; height: 801px; overflow: hidden; }
  body {
    background: var(--bg);
    font-family: "Source Sans 3", sans-serif;
    color: var(--ink);
    position: relative;
  }
  .card {
    position: absolute;
    top: 252px;
    width: 525px;
    height: 300px;
    background: var(--paper);
    border-radius: 14px;
    overflow: hidden;
    box-shadow: 0 14px 34px rgba(0,0,0,.5);
  }
  .card--front { left: 50px; }
  .card--back { left: 625px; }

  .company-name {
    position: absolute;
    font-weight: 600;
    color: var(--ink);
    line-height: 1;
  }
  .card--front .company-name { right: 34px; top: 40px; font-size: 32px; }
  .card--back .company-name { right: 40px; bottom: 110px; font-size: 56px; }

  .rule { position: absolute; left: 34px; height: 1px; background: var(--rule); }
  .rule--top { top: 100px; right: 34px; }
  .rule--mid { top: 188px; width: 200px; }

  .person { position: absolute; left: 34px; top: 130px; }
  .person__name {
    font-size: 22px; font-weight: 700; text-transform: uppercase; letter-spacing: 1px; line-height: 1.1;
  }
  .person__first { color: var(--teal); }
  .person__last { color: var(--orange); }
  .person__title { font-size: 14px; font-weight: 400; margin-top: 2px; }

  .contact { position: absolute; left: 34px; top: 200px; list-style: none; }
  .contact__item {
    display: flex; align-items: center; gap: 8px;
    font-size: 14px; line-height: 21px; font-weight: 400;
  }
  .contact__icon { width: 10px; height: 10px; flex: none; }

  .edge-mark { position: absolute; left: 0; top: 180px; width: 8px; height: 26px; background: var(--teal); }
  .edge-band { position: absolute; left: 0; right: 0; bottom: 0; height: 6px; background: var(--teal); }
</style>
</head>
<body>
  <section class="card card--front" aria-label="Business card front">
    <span class="company-name">Brightwell</span>
    <div class="rule rule--top"></div>

    <div class="person">
      <h1 class="person__name"><span class="person__first">Martin</span> <span class="person__last">Quelbrook</span></h1>
      <p class="person__title">CEO</p>
    </div>
    <div class="rule rule--mid"></div>

    <ul class="contact">
      <li class="contact__item">
        <svg class="contact__icon" viewBox="0 0 10 10" aria-hidden="true"><path d="M2 1h2l1 2.3-1.3.9a5.5 5.5 0 0 0 2.1 2.1l.9-1.3L9 6v2a1 1 0 0 1-1 1A7 7 0 0 1 1 2a1 1 0 0 1 1-1z" fill="var(--orange)"/></svg>
        <span>555-218-9403</span>
      </li>
      <li class="contact__item">
        <svg class="contact__icon" viewBox="0 0 10 10" aria-hidden="true"><rect x="0.5" y="2" width="9" height="6.5" rx="1" fill="var(--orange)"/><path d="M1 2.6 5 5.6 9 2.6" stroke="#fff" stroke-width="0.9" fill="none"/></svg>
        <span>martin@brightwellcivic.example</span>
      </li>
      <li class="contact__item">
        <svg class="contact__icon" viewBox="0 0 10 10" aria-hidden="true"><circle cx="5" cy="5" r="4.5" fill="var(--orange)"/><path d="M0.8 5h8.4M5 .6c-2.4 2.6-2.4 6.2 0 8.8M5 .6c2.4 2.6 2.4 6.2 0 8.8" stroke="#fff" stroke-width="0.7" fill="none"/></svg>
        <span>www.brightwellcivic.example</span>
      </li>
    </ul>

    <div class="edge-mark"></div>
    <div class="edge-band"></div>
  </section>

  <section class="card card--back" aria-label="Business card back">
    <span class="company-name">Brightwell</span>
  </section>
</body>
</html>
```